Create a memorable Web Design for real estate branding

we are a Minnepolis brokerage and boutique housing specialist with over 27 years of experience in the Global furnished housing industry, servicing the Greater Los Angeles area. Specializing in “warm environments” we offer a customized approach to satisfying our guests and client’s needs by offering a wide array of options in highly desirable areas. Additionally, Lantern Dwelling Partners offers assistance and expertise to home buyers, sellers and investors.

Industry/Entity Type

Real Estate

Number of Pages Required

1 page

Font styles to use
Serif
Sans Serif
Decorative

```html
<!DOCTYPE html>
<html lang="en">
<head>
<meta charset="utf-8">
<title>Marlowe Crest Real Estate</title>
<link rel="stylesheet" href="https://fonts.googleapis.com/css2?family=Cinzel:wght@400;700&family=Lato:wght@400;700&family=Marcellus&display=swap">
<style>
:root{
  --teal:#13a38b;
  --green:#95c83d;
  --ink:#222;
  --text:#444;
  --muted:#888;
  --line:#e4e4e4;
  --mist:#e9eef2;
  --footer:#2c2c2c;
  --white:#fff;
}
*{box-sizing:border-box;margin:0;padding:0}
html,body{width:1200px;height:3051px;overflow:hidden}
body{position:relative;font-family:'Lato',sans-serif;color:var(--text);background:var(--white)}
.abs{position:absolute}
/* header */
.site-header{top:0;left:0;width:1200px;height:114px;background:var(--white);border-bottom:2px solid #ddd}
.brand{left:85px;top:22px;color:var(--teal);font-family:'Lato',sans-serif;font-weight:700;line-height:1.05}
.brand .name{font-size:34px;display:block}
.brand .sub{font-size:22px;display:block;letter-spacing:2px}
.phone{right:85px;top:14px;display:flex;align-items:center;gap:12px;font-size:23px;color:var(--teal);font-weight:700}
.phone .dot{width:30px;height:30px;border-radius:50%;background:var(--teal);display:flex;align-items:center;justify-content:center}
.main-nav{right:85px;top:64px;display:flex;gap:34px;font-size:17px;font-weight:700;color:var(--ink)}
.main-nav .active{color:var(--teal)}
/* hero */
.hero{top:114px;left:0;width:1200px;height:557px;background:linear-gradient(180deg,#7b6f8c 0%,#8a6c52 35%,#5b4632 60%,#2e3526 85%,#1c2a22 100%)}
.hero-arrow{top:250px;color:var(--white)}
.hero-title{top:410px;left:0;width:1200px;text-align:center;font-family:'Marcellus',serif;font-size:34px;line-height:48px;color:var(--white);text-shadow:0 2px 6px rgba(0,0,0,.6)}
/* headings */
.section-title{left:0;width:1200px;text-align:center;font-family:'Cinzel',serif;font-size:38px;color:var(--ink)}
.section-title .accent{color:var(--teal)}
.rule{height:1px;background:var(--line);left:350px;width:500px}
/* welcome */
.welcome-text{top:826px;left:110px;width:980px;text-align:center;font-size:14.5px;line-height:32px;color:#333}
.btn{background:var(--teal);color:var(--white);font-weight:700;font-size:16px;display:flex;align-items:center;justify-content:center;border-radius:3px}
/* services */
.services{top:1068px;left:0;width:1200px;height:401px;background:var(--green)}
.services .section-title{color:var(--white);top:30px;font-size:33px}
.services .rule{top:92px;background:rgba(255,255,255,.4)}
.service{top:128px;width:300px;text-align:center;color:var(--white)}
.service .icon{width:88px;height:88px;border-radius:50%;background:var(--white);margin:0 auto;display:flex;align-items:center;justify-content:center}
.service h3{font-family:'Cinzel',serif;font-weight:400;font-size:22px;letter-spacing:1px;margin-top:22px}
.service p{font-size:14px;line-height:21px;margin-top:12px}
.service .plus{width:18px;height:18px;background:var(--white);margin:16px auto 0;color:var(--green);font-weight:700;font-size:16px;line-height:18px}
/* properties */
.card{top:1619px;width:334px;height:462px;border:1px solid var(--line);background:var(--white)}
.card .photo{height:197px;width:100%}
.card .tag{position:absolute;right:12px;top:180px;background:var(--teal);color:var(--white);font-size:14px;font-weight:700;padding:5px 14px}
.card h4{font-size:19px;font-weight:400;color:var(--ink);margin:20px 0 0 16px}
.card .price{color:var(--teal);font-size:15px;font-weight:700;margin:6px 0 0 16px}
.card .specs{margin-top:14px;border-top:1px solid var(--line);padding:8px 16px 6px}
.spec{display:flex;align-items:center;height:44px;font-size:14px;color:#333}
.spec svg{margin-right:16px}
.spec .count{margin-left:auto;width:24px;height:24px;border-radius:50%;background:#f0f0f0;border:1px solid #ddd;font-size:13px;display:flex;align-items:center;justify-content:center}
.card .loc{border-top:1px solid var(--line);height:44px;display:flex;align-items:center;padding-left:22px;font-size:14px;color:#333;gap:18px}
.pager{top:2114px;width:32px;height:20px;background:var(--teal);display:flex;align-items:center;justify-content:center}
/* testimonials */
.testimonials{top:2189px;left:0;width:1200px;height:421px;background:var(--mist)}
.quote{top:138px;width:503px;height:159px;background:var(--white);border-radius:12px;padding:18px 18px}
.quote h5{color:var(--teal);font-size:20px;font-weight:400}
.quote p{font-size:14px;line-height:21px;color:#333;margin-top:8px;width:430px}
.quote .mark{position:absolute;right:18px;top:24px;font-family:'Marcellus',serif;font-size:180px;line-height:150px;color:#e8ecef}
.quote .tail{position:absolute;left:130px;bottom:-22px;width:0;height:0;border-left:30px solid var(--white);border-bottom:22px solid transparent}
.avatar{top:309px;width:100px;height:100px;border-radius:50%;border:4px solid var(--white);box-shadow:0 0 0 1px #bbb;background:linear-gradient(160deg,#c9a58c,#6d5a4e)}
.author{top:343px;color:var(--teal);font-size:16px}
.stars{top:343px;color:#bbb;font-size:18px;letter-spacing:2px}
.t-arrow{top:205px;width:36px;height:36px;border-radius:50%;background:var(--white);border:1px solid #ccc;display:flex;align-items:center;justify-content:center}
/* newsletter */
.newsletter-title{top:2640px;left:152px;font-family:'Cinzel',serif;font-size:36px;color:var(--green);letter-spacing:1px}
.email-field{top:2643px;left:587px;width:386px;height:44px;border:1px solid #ddd;font-size:13px;color:#555;padding-left:18px;display:flex;align-items:center}
.signup{top:2643px;left:985px;width:130px;height:44px;background:var(--green);color:var(--white);font-weight:700;font-size:19px;display:flex;align-items:center;justify-content:center;border-radius:2px}
/* footer */
.site-footer{top:2720px;left:0;width:1200px;height:284px;background:var(--footer);color:#ccc}
.site-footer h6{font-family:'Cinzel',serif;font-size:17px;font-weight:400;color:var(--white);letter-spacing:1px;padding-bottom:10px;border-bottom:1px solid #444}
.col{top:38px}
.links li{list-style:none;font-size:12.5px;line-height:31px;color:#bbb}
.links li::before{content:"›";margin-right:6px;color:#777}
.links li.active{color:var(--teal)}
.contact p{font-size:12.5px;line-height:19px}
.contact .label{color:var(--teal);font-weight:700}
.contact .row{display:flex;align-items:center;gap:12px;margin-top:10px;font-size:15px}
.map{width:284px;height:170px;border:4px solid #fff;background:linear-gradient(135deg,#cfe0ea,#e6dfc6 50%,#c8d9b5)}
.social{display:flex;align-items:center;gap:14px;margin-top:18px}
.social .dot{width:28px;height:28px;border-radius:50%}
.social b{display:block;font-size:14px;font-weight:400;color:var(--white)}
.social small{display:block;font-size:10px;color:#aaa}
.copyright{top:3004px;left:0;width:1200px;height:47px;background:var(--teal);color:var(--white);font-size:14px;display:flex;align-items:center;justify-content:center}
</style>
</head>
<body>

<header class="site-header abs">
  <div class="brand abs"><span class="name">Marlowe Crest</span><span class="sub">Real Estate</span></div>
  <div class="phone abs">
    <span class="dot"><svg width="16" height="16" viewBox="0 0 24 24"><path fill="#fff" d="M6.6 10.8a15 15 0 0 0 6.6 6.6l2.2-2.2c.3-.3.7-.4 1-.2 1.1.4 2.3.6 3.6.6.6 0 1 .4 1 1V20c0 .6-.4 1-1 1A17 17 0 0 1 3 4c0-.6.4-1 1-1h3.5c.6 0 1 .4 1 1 0 1.3.2 2.5.6 3.6.1.3 0 .7-.2 1z"/></svg></span>
    555 014 2260
  </div>
  <nav class="main-nav abs">
    <span class="active">Home</span><span>About Us</span><span>Properties</span><span>Resources</span><span>Testimonials</span><span>Contact Us</span>
  </nav>
</header>

<section class="hero abs" role="img" aria-label="Evening photograph of a lit Mediterranean-style villa with palm trees and a stone courtyard">
  <svg class="hero-arrow abs" style="left:34px" width="20" height="40" viewBox="0 0 20 40"><path d="M18 2 2 20l16 18" stroke="#fff" stroke-width="2.5" fill="none"/></svg>
  <svg class="hero-arrow abs" style="right:34px" width="20" height="40" viewBox="0 0 20 40"><path d="M2 2l16 18L2 38" stroke="#fff" stroke-width="2.5" fill="none"/></svg>
  <h1 class="hero-title abs" style="top:296px;font-weight:400">We Are A Brokerage &amp; Boutique Housing Specialist With Over<br>27 Years Of Experience In Greater Los Angeles Area</h1>
</section>

<h2 class="section-title abs" style="top:722px;font-weight:400">Welcome To <span class="accent">Marlowe Crest Real Estate</span></h2>
<div class="rule abs" style="top:793px"></div>
<p class="welcome-text abs">Lorem ipsum dolor sit amet, consectetuer adipiscing elit, sed diam nonummy nibh euismod tincidunt ut laoreet dolore magna aliquam erat volutpat. Ut wisi enim ad minim veniam, quis nostrud exerci tation ullamcorper suscipit lobortis nisl ut aliquip ex ea commodo consequat. Duis autem vel eum iriure dolor in hendrerit in vulputate velit esse molestie consequat, vel illum dolore eu feugiat nulla facilisis at vero eros et accumsan et iusto odio dignissim qui l dolore teconsequat. Duis autem feugiat nulla feugait nulla facilisi.</p>
<div class="btn abs" style="top:976px;left:543px;width:114px;height:38px">Read More</div>

<section class="services abs">
  <h2 class="section-title abs" style="font-weight:400">Our Housing Group offers assistance &amp; expertise To</h2>
  <div class="rule abs"></div>
  <div class="service abs" style="left:100px">
    <div class="icon"><svg width="50" height="50" viewBox="0 0 50 50" fill="none" stroke="#95c83d" stroke-width="3"><path d="M6 24 25 8l19 16"/><path d="M12 20v22h26V20"/><text x="25" y="37" text-anchor="middle" font-family="Lato,sans-serif" font-size="14" font-weight="700" fill="#95c83d" stroke="none">$</text></svg></div>
    <h3>Home Buyers</h3>
    <p>Lorem ipsum dolor sit amet,<br>consectetuer adipiscing elit, sed diam<br>nonum nibh magna.</p>
    <div class="plus">+</div>
  </div>
  <div class="service abs" style="left:440px">
    <div class="icon"><svg width="50" height="50" viewBox="0 0 50 50" fill="none" stroke="#95c83d" stroke-width="3"><path d="M12 20 25 9l13 11"/><path d="M16 18v12h18V18"/><path d="M6 38c6 0 10-4 16-4h10c2 0 2 4 0 4h-8m-18 6h26l12-10"/></svg></div>
    <h3>Home Sellers</h3>
    <p>Lorem ipsum dolor sit amet,<br>consectetuer adipiscing elit, sed diam<br>nonum nibh magna.</p>
    <div class="plus">+</div>
  </div>
  <div class="service abs" style="left:780px">
    <div class="icon"><svg width="50" height="50" viewBox="0 0 50 50" fill="none" stroke="#95c83d" stroke-width="3"><rect x="10" y="12" width="30" height="26" rx="3"/><circle cx="25" cy="25" r="8"/><path d="M6 40h38"/></svg></div>
    <h3>Home Investors</h3>
    <p>Lorem ipsum dolor sit amet,<br>consectetuer adipiscing elit, sed diam<br>nonum nibh magna.</p>
    <div class="plus">+</div>
  </div>
</section>

<h2 class="section-title abs" style="top:1515px;font-weight:400">Featured <span class="accent">Property</span></h2>
<div class="rule abs" style="top:1577px"></div>

<article class="card abs" style="left:85px">
  <div class="photo" role="img" aria-label="Bright modern bedroom interior with white furniture and red accents" style="background:linear-gradient(160deg,#d8d6d2,#8f8883)"></div>
  <span class="tag">ON RENT</span>
  <h4>Sabestian Villa, NY</h4>
  <div class="price">$1900</div>
  <div class="specs">
    <div class="spec"><svg width="18" height="16" viewBox="0 0 18 16" fill="none" stroke="#777" stroke-width="1.4"><path d="M1 8h16v3a4 4 0 0 1-4 4H5a4 4 0 0 1-4-4zM3 8V3a2 2 0 0 1 4 0"/></svg>Bathrooms<span class="count">2</span></div>
    <div class="spec"><svg width="18" height="14" viewBox="0 0 18 14" fill="none" stroke="#777" stroke-width="1.4"><path d="M1 2v11m0-3h16v3M1 7h16v3M4 5h4v2"/></svg>Beds<span class="count">2</span></div>
    <div class="spec"><svg width="18" height="16" viewBox="0 0 18 16" fill="none" stroke="#777" stroke-width="1.4"><path d="M1 15V6l8-5 8 5v9M4 15V9h10v6"/></svg>Garages<span class="count">2</span></div>
  </div>
  <div class="loc"><svg width="12" height="16" viewBox="0 0 12 16"><path fill="#13a38b" d="M6 0a6 6 0 0 1 6 6c0 4-6 10-6 10S0 10 0 6a6 6 0 0 1 6-6zm0 4a2 2 0 1 0 0 4 2 2 0 0 0 0-4z"/></svg>United States / idaho</div>
</article>

<article class="card abs" style="left:433px">
  <div class="photo" role="img" aria-label="Luxury house with a blue pool at dusk" style="background:linear-gradient(180deg,#7aa6d8,#c9a57b 60%,#3f8fb8)"></div>
  <span class="tag">ON SALE</span>
  <h4>Bill Tower, Survey, NJ</h4>
  <div class="price">$990,78</div>
  <div class="specs">
    <div class="spec"><svg width="18" height="16" viewBox="0 0 18 16" fill="none" stroke="#777" stroke-width="1.4"><path d="M1 8h16v3a4 4 0 0 1-4 4H5a4 4 0 0 1-4-4zM3 8V3a2 2 0 0 1 4 0"/></svg>Bathrooms<span class="count">3</span></div>
    <div class="spec"><svg width="18" height="14" viewBox="0 0 18 14" fill="none" stroke="#777" stroke-width="1.4"><path d="M1 2v11m0-3h16v3M1 7h16v3M4 5h4v2"/></svg>Beds<span class="count">4</span></div>
    <div class="spec"><svg width="18" height="16" viewBox="0 0 18 16" fill="none" stroke="#777" stroke-width="1.4"><path d="M1 15V6l8-5 8 5v9M4 15V9h10v6"/></svg>Garages<span class="count">2</span></div>
  </div>
  <div class="loc"><svg width="12" height="16" viewBox="0 0 12 16"><path fill="#13a38b" d="M6 0a6 6 0 0 1 6 6c0 4-6 10-6 10S0 10 0 6a6 6 0 0 1 6-6zm0 4a2 2 0 1 0 0 4 2 2 0 0 0 0-4z"/></svg>United States / South Dakota</div>
</article>

<article class="card abs" style="left:781px">
  <div class="photo" role="img" aria-label="Desert-style stone house with palm garden under blue sky" style="background:linear-gradient(180deg,#4f8fd6,#b89a72 55%,#6c7a46)"></div>
  <span class="tag">ON SALE</span>
  <h4>Florida 5, Pinecrest, FL</h4>
  <div class="price">$125,79</div>
  <div class="specs">
    <div class="spec"><svg width="18" height="16" viewBox="0 0 18 16" fill="none" stroke="#777" stroke-width="1.4"><path d="M1 8h16v3a4 4 0 0 1-4 4H5a4 4 0 0 1-4-4zM3 8V3a2 2 0 0 1 4 0"/></svg>Bathrooms<span class="count">2</span></div>
    <div class="spec"><svg width="18" height="14" viewBox="0 0 18 14" fill="none" stroke="#777" stroke-width="1.4"><path d="M1 2v11m0-3h16v3M1 7h16v3M4 5h4v2"/></svg>Beds<span class="count">2</span></div>
    <div class="spec"><svg width="18" height="16" viewBox="0 0 18 16" fill="none" stroke="#777" stroke-width="1.4"><path d="M1 15V6l8-5 8 5v9M4 15V9h10v6"/></svg>Garages<span class="count">1</span></div>
  </div>
  <div class="loc"><svg width="12" height="16" viewBox="0 0 12 16"><path fill="#13a38b" d="M6 0a6 6 0 0 1 6 6c0 4-6 10-6 10S0 10 0 6a6 6 0 0 1 6-6zm0 4a2 2 0 1 0 0 4 2 2 0 0 0 0-4z"/></svg>United States / Minnesota</div>
</article>

<div class="pager abs" style="left:561px"><svg width="20" height="10" viewBox="0 0 20 10"><path d="M19 5H2m4-4L2 5l4 4" stroke="#fff" stroke-width="1.6" fill="none"/></svg></div>
<div class="pager abs" style="left:607px"><svg width="20" height="10" viewBox="0 0 20 10"><path d="M1 5h17m-4-4 4 4-4 4" stroke="#fff" stroke-width="1.6" fill="none"/></svg></div>

<section class="testimonials abs">
  <h2 class="section-title abs" style="top:35px;font-weight:400">Client <span class="accent">Testimonials</span></h2>
  <div class="rule abs" style="top:96px"></div>
  <div class="t-arrow abs" style="left:24px"><svg width="10" height="14" viewBox="0 0 10 14"><path d="M8 1 2 7l6 6" stroke="#777" stroke-width="1.6" fill="none"/></svg></div>
  <div class="t-arrow abs" style="right:24px"><svg width="10" height="14" viewBox="0 0 10 14"><path d="M2 1l6 6-6 6" stroke="#777" stroke-width="1.6" fill="none"/></svg></div>

  <div class="quote abs" style="left:85px">
    <span class="mark">”</span>
    <h5>Lorem ipsum dolor sit amet consectet</h5>
    <p>Lorem ipsum dolor sit amet, consectet uer adipiscing elit, sed diam nonummy nibh euis mod tincidun nt ut laoreetml dolore magna aliquam erat volutpat.</p>
    <span class="tail"></span>
  </div>
  <div class="avatar abs" style="left:112px" role="img" aria-label="Portrait of a smiling client"></div>
  <div class="author abs" style="left:262px">- Miss Elena Varrow</div>
  <div class="stars abs" style="left:478px">★★★★★</div>

  <div class="quote abs" style="left:612px">
    <span class="mark">”</span>
    <h5>Lorem ipsum dolor sit amet consectet</h5>
    <p>Lorem ipsum dolor sit amet, consectet uer adipiscing elit, sed diam nonummy nibh euis mod tincidun nt ut laoreetml dolore magna aliquam erat volutpat.</p>
    <span class="tail"></span>
  </div>
  <div class="avatar abs" style="left:639px;background:linear-gradient(160deg,#b48f76,#3e3a3a)" role="img" aria-label="Portrait of a smiling client"></div>
  <div class="author abs" style="left:788px">- Mr. Tobin Aldercott</div>
  <div class="stars abs" style="left:1005px">★★★★★</div>
</section>

<svg class="abs" style="left:84px;top:2640px" width="52" height="52" viewBox="0 0 52 52"><circle cx="26" cy="26" r="24" fill="none" stroke="#95c83d" stroke-width="2"/><rect x="14" y="18" width="24" height="16" fill="#95c83d"/><path d="M14 18l12 9 12-9" stroke="#fff" stroke-width="1.6" fill="none"/></svg>
<div class="newsletter-title abs">Newsletter Signup</div>
<svg class="abs" style="left:540px;top:2636px" width="30" height="58" viewBox="0 0 30 58"><path d="M2 2l26 27L2 56" stroke="#95c83d" stroke-width="2" fill="none"/></svg>
<div class="email-field abs">Your email address</div>
<div class="signup abs">Sign Up</div>

<footer class="site-footer abs">
  <div class="col abs" style="left:88px;width:140px">
    <h6>Quick Links</h6>
    <ul class="links" style="margin-top:8px">
      <li class="active">Home</li><li>About Us</li><li>Properties</li><li>Resources</li><li>Testimonials</li><li>Contact Us</li>
    </ul>
  </div>
  <div class="col abs contact" style="left:283px;width:210px">
    <h6>Contact Details</h6>
    <p class="label" style="margin-top:10px">Marlowe Crest Real Estate</p>
    <p>16 Lorem ipsum dolor sit amet,<br>Sed benetion, Street no-123456</p>
    <div class="row"><svg width="14" height="14" viewBox="0 0 24 24"><path fill="#ccc" d="M6.6 10.8a15 15 0 0 0 6.6 6.6l2.2-2.2c.3-.3.7-.4 1-.2 1.1.4 2.3.6 3.6.6.6 0 1 .4 1 1V20c0 .6-.4 1-1 1A17 17 0 0 1 3 4c0-.6.4-1 1-1h3.5c.6 0 1 .4 1 1 0 1.3.2 2.5.6 3.6.1.3 0 .7-.2 1z"/></svg>555-014-1789</div>
    <div class="row"><svg width="14" height="14" viewBox="0 0 14 14"><path fill="#ccc" d="M3 0h8v4H3zM1 5h12v6h-2v3H3v-3H1zm3 4v4h6V9z"/></svg>555-014-7890</div>
    <div class="row" style="font-size:12.5px"><svg width="14" height="10" viewBox="0 0 14 10"><rect width="14" height="10" fill="#ccc"/><path d="M0 0l7 6 7-6" stroke="#2c2c2c" fill="none"/></svg>info@marlowecrest.example</div>
  </div>
  <div class="col abs" style="left:568px;width:288px">
    <h6>Location Map</h6>
    <div class="map" style="margin-top:14px" role="img" aria-label="Street map of the office location with a red pin"></div>
  </div>
  <div class="col abs" style="left:938px;width:178px">
    <h6 style="text-align:center">Social Connect</h6>
    <div class="social" style="margin-top:22px"><span class="dot" style="background:#3b5b9a"></span><div><b>COMMUNITY</b><small>BECOME A FAN</small></div></div>
    <div class="social"><span class="dot" style="background:#1b7bb5"></span><div><b>NETWORK</b><small>JOIN US ON</small></div></div>
    <div class="social"><span class="dot" style="background:#2ba3e0"></span><div><b>UPDATES</b><small>JOIN US ON</small></div></div>
  </div>
</footer>
<div class="copyright abs">Copyright © 2016 Marlowe Crest Real Estate . All Rights Reserved.</div>

</body>
</html>
```